Board Presentation template

Design a simple and clean PowerPoint slide templates for a Board meeting. The slides should have predominantly white backgrounds and use the colors of our Logo (attached): Tones of grey and orange and blue.
The company name is called Keystone Lane Gauging.
It sell, calibrate, service and repair industrial and commercial scales of all types. In particular, Truck scales, floor scales, counting scales and benchtop scales.
There is no website for Keystone Lane Gauging, but we have three affiliates that have their own websites:
https://www.fernwaybalance.example/
https://meadowlarkhandlingandmassing.example/
https://tvbalance.example/
Target Market(s)
Industrial and Commercial Weighing systems
Industry/Entity Type
Look and feel

```html
<!DOCTYPE html>
<html lang="en">
<head>
<meta charset="utf-8">
<title>Keystone Lane Gauging — Board Presentation</title>
<link href="https://fonts.googleapis.com/css2?family=Fira+Sans:wght@400;500;600;700&family=Poppins:wght@400;500;600&display=swap" rel="stylesheet">
<style>
:root{
  --canvas:#efefef;
  --white:#ffffff;
  --blue:#2a5d8a;
  --red:#d3302f;
  --bar:#4b5661;
  --ink:#1f2328;
  --muted:#3c4248;
  --line:#c9ced3;
}
*{box-sizing:border-box;margin:0;padding:0}
html,body{width:1105px;height:1200px;overflow:hidden;background:var(--canvas)}
body{position:relative;font-family:"Poppins",sans-serif;color:var(--ink)}
.slide{position:absolute;width:481px;height:270px;background:var(--white);overflow:hidden}
.col-l{left:48px}.col-r{left:578px}
.row1{top:27px}.row2{top:311px}.row3{top:597px}.row4{top:882px}
.footer{position:absolute;left:0;bottom:0;width:100%;height:21px;background:var(--bar)}
.footer .mark{position:absolute;left:9px;top:4px;width:12px;height:12px;border:1.4px solid #fff;border-radius:50%}
.footer .num{position:absolute;right:6px;top:4px;width:13px;height:13px;border-radius:50%;background:var(--red);color:#fff;font:600 7px/13px "Poppins",sans-serif;text-align:center}
.accent{position:absolute;height:3px;width:30px;background:var(--red)}
.title{position:absolute;left:0;width:100%;text-align:center;font:600 22px/1 "Fira Sans",sans-serif;color:var(--blue)}
.photo{position:absolute}

/* title slide */
.hero-photo{left:0;top:0;width:100%;height:100%;background:linear-gradient(110deg,#59636e 0%,#8e96a0 30%,#c9b79a 60%,#e7d3b3 100%)}
.hero-panel{position:absolute;left:0;top:0}
.brand{position:absolute;text-align:center}
.brand-dot{position:absolute;left:341px;top:38px;width:38px;height:38px;border-radius:50%;border:3px solid #4a545e}
.hero .brand-name{left:274px;width:172px;top:110px;font:600 15px/1.05 "Fira Sans",sans-serif;color:#3f4952;letter-spacing:.5px}
.hero-head{position:absolute;left:250px;width:216px;top:155px;text-align:center;font:700 19px/1.15 "Fira Sans",sans-serif;color:#15181b;letter-spacing:.5px}
.hero-tag{position:absolute;left:196px;width:276px;top:206px;text-align:center;font:400 11px/1.55 "Fira Sans",sans-serif;color:#15181b}

/* about */
.about-photo{left:17px;top:19px;width:206px;height:215px;border-radius:10px;background:linear-gradient(160deg,#6aa6d9 0%,#bcd3e4 45%,#e0a22a 60%,#7d7466 100%)}
.about .accent{left:240px;top:29px}
.about h2{position:absolute;left:240px;top:43px;font:600 21px/.98 "Fira Sans",sans-serif;color:var(--blue)}
.about .lead{position:absolute;left:240px;top:94px;width:200px;font:600 9.8px/1.4 "Poppins",sans-serif;color:var(--red)}
.about .body{position:absolute;left:240px;top:127px;width:225px;font:400 6.6px/1.94 "Poppins",sans-serif;color:var(--muted)}

/* breaking */
.break-photo{left:0;top:0;width:100%;height:100%;background:linear-gradient(100deg,#102a44 0%,#1e466c 45%,#2a5478 70%,#163451 100%)}
.break .accent{background:#fff;left:226px;top:119px}
.break h2{position:absolute;left:0;width:100%;top:130px;text-align:center;font:600 21px/1 "Fira Sans",sans-serif;color:#fff;letter-spacing:.4px}

/* what we do */
.what .accent{left:225px;top:19px}
.what .title{top:30px}
.services{position:absolute;left:0;top:79px;width:100%;display:flex}
.service{flex:1;height:155px;text-align:center;border-right:1px solid var(--line)}
.service:last-child{border-right:none}
.service svg{display:block;margin:10px auto 0;width:34px;height:34px}
.service h3{margin-top:8px;font:500 12px/1 "Fira Sans",sans-serif;color:var(--red)}
.service p{margin:7px auto 0;width:100px;font:400 7.9px/1.55 "Fira Sans",sans-serif;color:var(--muted)}

/* solutions */
.solutions .accent{left:226px;top:15px}
.solutions .title{top:25px}
.solutions .sub{position:absolute;left:0;width:100%;top:53px;text-align:center;font:400 7.6px/1 "Poppins",sans-serif;color:var(--ink)}
.sol-card{position:absolute;width:224px;height:76px;border:1px solid var(--line)}
.sol-card svg{position:absolute;left:9px;top:13px;width:15px;height:15px}
.sol-card h3{position:absolute;left:34px;top:12px;font:500 12.5px/1 "Fira Sans",sans-serif;color:var(--blue)}
.sol-card p{position:absolute;left:35px;top:33px;width:178px;font:400 6.9px/1.45 "Fira Sans",sans-serif;color:var(--muted)}

/* affiliates */
.affiliates .accent{left:226px;top:16px}
.affiliates .title{top:27px}
.aff-card{position:absolute;top:58px;width:148px;height:180px;border:1px solid var(--line);text-align:center}
.aff-logo{position:relative;height:84px;display:flex;align-items:center;justify-content:center;gap:5px;padding:0 8px}
.aff-logo i{flex:none;width:14px;height:14px;border-radius:50%;background:var(--red)}
.aff-logo span{font:600 10px/1.15 "Fira Sans",sans-serif;color:var(--red);text-align:left}
.aff-card h3{margin-top:10px;font:500 12px/1.2 "Fira Sans",sans-serif;color:var(--blue)}
.aff-card p{margin:7px auto 0;width:132px;font:400 7.4px/1.45 "Fira Sans",sans-serif;color:var(--muted)}

/* data */
.data .accent{left:226px;top:12px}
.data .title{top:22px}
.chart{position:absolute;left:0;top:58px}
.data-copy{position:absolute;left:241px;top:65px;width:230px}
.data-copy .lead{font:500 8.3px/1.55 "Fira Sans",sans-serif;color:var(--muted)}
.data-copy h3{margin-top:10px;font:500 12.5px/1 "Fira Sans",sans-serif;color:var(--red)}
.data-copy h3.blue{color:var(--blue)}
.data-copy p{margin-top:6px;font:400 7.4px/1.5 "Fira Sans",sans-serif;color:var(--muted)}

/* thank you */
.thanks-photo{left:0;top:0;width:100%;height:100%;background:linear-gradient(105deg,#1b1d20 0%,#34383d 50%,#2a2d31 100%)}
.thanks .accent{background:#fff;left:25px;top:65px}
.thanks h2{position:absolute;left:25px;top:76px;font:600 22px/1 "Fira Sans",sans-serif;color:#fff}
.thanks p{position:absolute;left:25px;top:107px;width:220px;font:400 10px/1.65 "Poppins",sans-serif;color:#fff}
.socials{position:absolute;left:22px;top:185px;display:flex;gap:16px}
.socials span{width:22px;height:22px;border:1.3px solid #fff;border-radius:50%}
.thanks .brand-dot{left:347px;top:63px;width:52px;height:52px;border:4px solid #fff}
.thanks .brand-name{left:283px;width:180px;top:150px;font:600 19px/1.05 "Fira Sans",sans-serif;color:#fff}
</style>
</head>
<body>

<!-- Title -->
<section class="slide col-l row1 hero">
  <div class="photo hero-photo" role="img" aria-label="Photo of a white semi truck parked on a truck scale at a warehouse loading dock at sunset"></div>
  <svg class="hero-panel" width="481" height="270" viewBox="0 0 481 270"><polygon points="304,24 476,24 476,264 140,264" fill="#ffffff" fill-opacity=".9"/></svg>
  <div class="brand-dot"></div>
  <div class="brand brand-name">KEYSTONE LANE<br>GAUGING</div>
  <h1 class="hero-head">KEYSTONE LANE<br>GAUGING.</h1>
  <p class="hero-tag">We sell, calibrate, service and repair industrial and commercial scales of all types</p>
</section>

<!-- About -->
<section class="slide col-l row2 about">
  <div class="photo about-photo" role="img" aria-label="Photo of a yellow dump truck standing on a truck scale platform under a blue sky"></div>
  <div class="accent"></div>
  <h2>About Keystone<br>Lane Gauging</h2>
  <p class="lead">Nemo enim ipsam voluptatem quia voluptas sit aspernatur aut</p>
  <p class="body">Sed ut perspiciatis unde omnis iste natus error sit voluptatem accusantium doloremque laudantium, totam rem aperiam, eaque ipsa quae ab illo inventore veritatis et quasi architecto beatae vitae dicta sunt explicabo. Nemo enim ipsam voluptatem quia voluptas sit aspernatur aut odit aut fugit, sed quia consequuntur magni dolores eos qui ratione voluptatem sequi nesciunt. Neque porro quisquam est, qui dolorem ipsum quia dolor sit amet, consectetur.</p>
  <div class="footer"><span class="mark"></span><span class="num">2</span></div>
</section>

<!-- Breaking -->
<section class="slide col-l row3 break">
  <div class="photo break-photo" role="img" aria-label="Blue-toned photo of a trailer truck inside a warehouse"></div>
  <div class="accent"></div>
  <h2>Breaking Content Slide</h2>
</section>

<!-- What we do -->
<section class="slide col-l row4 what">
  <div class="accent"></div>
  <h2 class="title">What We Do</h2>
  <div class="services">
    <div class="service">
      <svg viewBox="0 0 34 34" fill="none" stroke="#1f2328" stroke-width="1.2"><rect x="2" y="21" width="28" height="4"/><line x1="5" y1="25" x2="5" y2="29"/><line x1="27" y1="25" x2="27" y2="29"/><rect x="5" y="14" width="8" height="7"/><rect x="14" y="16" width="7" height="5"/><line x1="26" y1="21" x2="26" y2="8"/><circle cx="26" cy="5" r="3.5"/></svg>
      <h3>Calibrate</h3>
      <p>Sed ut perspiciatis unde omnis iste natus error sit voluptatem accusantium doloremque enim ipsam voluptatem quia</p>
    </div>
    <div class="service">
      <svg viewBox="0 0 34 34" fill="none" stroke="#1f2328" stroke-width="1.4"><line x1="6" y1="6" x2="28" y2="28"/><line x1="28" y1="6" x2="6" y2="28"/><circle cx="26" cy="8" r="4"/><rect x="3" y="3" width="6" height="6"/><rect x="24" y="24" width="6" height="6"/><circle cx="8" cy="26" r="4"/></svg>
      <h3>Service &amp; Repair</h3>
      <p>Sed ut perspiciatis unde omnis iste natus error sit voluptatem accusantium doloremque enim ipsam voluptatem quia</p>
    </div>
    <div class="service">
      <svg viewBox="0 0 34 34" fill="none" stroke="#1f2328" stroke-width="1.3"><rect x="9" y="3" width="16" height="9"/><rect x="12" y="6" width="10" height="3"/><line x1="17" y1="12" x2="17" y2="26"/><rect x="4" y="26" width="26" height="3"/><line x1="6" y1="29" x2="6" y2="31"/><line x1="28" y1="29" x2="28" y2="31"/></svg>
      <h3>Industrial Scales</h3>
      <p>Sed ut perspiciatis unde omnis iste natus error sit voluptatem accusantium doloremque enim ipsam voluptatem quia</p>
    </div>
    <div class="service">
      <svg viewBox="0 0 34 34" fill="none" stroke="#1f2328" stroke-width="1.2"><rect x="2" y="8" width="18" height="14"/><path d="M20 12h6l4 5v5H20z"/><circle cx="7" cy="24" r="2.5"/><circle cx="25" cy="24" r="2.5"/><rect x="1" y="27" width="31" height="3"/><line x1="31" y1="27" x2="31" y2="4"/><rect x="28" y="2" width="5" height="4"/></svg>
      <h3>Commercial Scales</h3>
      <p>Sed ut perspiciatis unde omnis iste natus error sit voluptatem accusantium doloremque enim ipsam voluptatem quia</p>
    </div>
  </div>
  <div class="footer"><span class="mark"></span><span class="num">4</span></div>
</section>

<!-- Solutions -->
<section class="slide col-r row1 solutions">
  <div class="accent"></div>
  <h2 class="title">Our Solutions</h2>
  <p class="sub">Nemo enim ipsam voluptatem quia voluptas sit aspernatur aut odit aut fugit.</p>
  <div class="sol-card" style="left:14px;top:77px">
    <svg viewBox="0 0 16 16" fill="none" stroke="#d3302f" stroke-width="1.3"><circle cx="8" cy="8" r="7"/><path d="M4.6 8.2l2.3 2.2 4.5-4.6"/></svg>
    <h3>Nemo enim ipsam</h3>
    <p>Neque porro quisquam est, qui dolorem ipsum quia dolor sit amet, consectetur, adipisci velit numquam eius modi tempora incidunt.</p>
  </div>
  <div class="sol-card" style="left:244px;top:77px">
    <svg viewBox="0 0 16 16" fill="none" stroke="#d3302f" stroke-width="1.3"><circle cx="8" cy="8" r="7"/><path d="M4.6 8.2l2.3 2.2 4.5-4.6"/></svg>
    <h3>Nemo enim ipsam</h3>
    <p>Neque porro quisquam est, qui dolorem ipsum quia dolor sit amet, consectetur, adipisci velit numquam eius modi tempora incidunt.</p>
  </div>
  <div class="sol-card" style="left:14px;top:158px">
    <svg viewBox="0 0 16 16" fill="none" stroke="#d3302f" stroke-width="1.3"><circle cx="8" cy="8" r="7"/><path d="M4.6 8.2l2.3 2.2 4.5-4.6"/></svg>
    <h3>Nemo enim ipsam</h3>
    <p>Neque porro quisquam est, qui dolorem ipsum quia dolor sit amet, consectetur, adipisci velit numquam eius modi tempora incidunt.</p>
  </div>
  <div class="sol-card" style="left:244px;top:158px">
    <svg viewBox="0 0 16 16" fill="none" stroke="#d3302f" stroke-width="1.3"><circle cx="8" cy="8" r="7"/><path d="M4.6 8.2l2.3 2.2 4.5-4.6"/></svg>
    <h3>Nemo enim ipsam</h3>
    <p>Neque porro quisquam est, qui dolorem ipsum quia dolor sit amet, consectetur, adipisci velit numquam eius modi tempora incidunt.</p>
  </div>
  <div class="footer"><span class="mark"></span><span class="num">5</span></div>
</section>

<!-- Affiliates -->
<section class="slide col-r row2 affiliates">
  <div class="accent"></div>
  <h2 class="title">Affiliates</h2>
  <div class="aff-card" style="left:11px">
    <div class="aff-logo"><i></i><span>FERNWAY<br>BALANCE</span></div>
    <h3>Fernway Balance<br>Service</h3>
    <p>Nemo enim ipsam voluptatem quia voluptas sit aspernatur aut odit aut fugit, sed quia consequuntur mag veritatis et quasi architecto</p>
  </div>
  <div class="aff-card" style="left:166px">
    <div class="aff-logo"><i style="background:#3a3f45"></i><span style="color:#3a3f45">MEADOWLARK<br>HANDLING</span></div>
    <h3>Meadowlark Handling<br>&amp; Massing</h3>
    <p>Nemo enim ipsam voluptatem quia voluptas sit aspernatur aut odit aut fugit, sed quia consequuntur mag veritatis et quasi architecto</p>
  </div>
  <div class="aff-card" style="left:322px">
    <div class="aff-logo"><i></i><span>T&amp;V<br>BALANCE CO.</span></div>
    <h3>T&amp;V<br>Balance</h3>
    <p>Nemo enim ipsam voluptatem quia voluptas sit aspernatur aut odit aut fugit, sed quia consequuntur mag veritatis et quasi architecto</p>
  </div>
  <div class="footer"><span class="mark"></span><span class="num">6</span></div>
</section>

<!-- Data -->
<section class="slide col-r row3 data">
  <div class="accent"></div>
  <h2 class="title">Data Analysis</h2>
  <svg class="chart" width="230" height="190" viewBox="0 0 230 190" font-family="Poppins, sans-serif" font-size="4.5" fill="#1f2328">
    <g text-anchor="end">
      <text x="18" y="10">100%</text><text x="18" y="26.3">90%</text><text x="18" y="42.6">80%</text><text x="18" y="58.9">70%</text><text x="18" y="75.2">60%</text><text x="18" y="91.5">50%</text><text x="18" y="107.8">40%</text><text x="18" y="124.1">30%</text><text x="18" y="140.4">20%</text><text x="18" y="156.7">10%</text><text x="18" y="173">0%</text>
    </g>
    <line x1="21" y1="8" x2="21" y2="171" stroke="#c9ced3" stroke-width=".5"/>
    <line x1="21" y1="171" x2="224" y2="171" stroke="#c9ced3" stroke-width=".5"/>
    <g fill="#d3302f">
      <rect x="29" y="65" width="9" height="106"/><rect x="58" y="81.4" width="9" height="89.6"/><rect x="87" y="24.3" width="9" height="146.7"/><rect x="116" y="86.2" width="9" height="84.8"/><rect x="145" y="118.8" width="9" height="52.2"/><rect x="174" y="47.1" width="9" height="123.9"/><rect x="203" y="9.6" width="9" height="161.4"/>
    </g>
    <g fill="#2a5d8a">
      <rect x="38" y="105.8" width="9" height="65.2"/><rect x="67" y="39" width="9" height="132"/><rect x="96" y="133.5" width="9" height="37.5"/><rect x="125" y="105.8" width="9" height="65.2"/><rect x="154" y="91.1" width="9" height="79.9"/><rect x="183" y="65" width="9" height="106"/><rect x="212" y="153.1" width="9" height="17.9"/>
    </g>
    <g text-anchor="middle">
      <text x="38" y="181">2018</text><text x="67" y="181">2019</text><text x="96" y="181">2020</text><text x="125" y="181">2021</text><text x="154" y="181">2022</text><text x="183" y="181">2023</text><text x="212" y="181">2024</text>
    </g>
  </svg>
  <div class="data-copy">
    <p class="lead">Nemo enim ipsam voluptatem quia voluptas sit aspernatur aut odit aut fugit, sed quia consequuntur magni dolores eos qui.</p>
    <h3>Neque porro quisquam est</h3>
    <p>Nemo enim ipsam voluptatem quia voluptas sit aspernatur aut odit aut fugit, sed quia consequuntur mag veritatis et quasi architecto beatae vitae dicta sunt</p>
    <h3 class="blue">Neque porro quisquam est</h3>
    <p>Nemo enim ipsam voluptatem quia voluptas sit aspernatur aut odit aut fugit, sed quia consequuntur mag veritatis et quasi architecto beatae vitae dicta sunt</p>
  </div>
  <div class="footer"><span class="mark"></span><span class="num">7</span></div>
</section>

<!-- Thank you -->
<section class="slide col-r row4 thanks">
  <div class="photo thanks-photo" role="img" aria-label="Dark photo of a semi truck parked inside an industrial garage"></div>
  <div class="accent"></div>
  <h2>Thank You</h2>
  <p>Nemo enim ipsam voluptatem quia voluptas sit aspernatur aut odit aut fugit, sed quia consequuntur magni dolores eos.</p>
  <div class="socials"><span></span><span></span><span></span></div>
  <div class="brand-dot"></div>
  <div class="brand brand-name">KEYSTONE LANE<br>GAUGING</div>
</section>

</body>
</html>
```